Create a premium soap bar box bar design for an all-natural, men's skincare brand.

We are launching a men’s premium, natural soap bar and skincare business. To start, we will be launching cold-press, all-natural soap bars with a few additional products such as lotions. We plan to expand our line into additional skincare products such as face exfoliants, moisturizers and cleansers that target basic needs such as anti-aging, clarifying and hydrating.

Our target audience is men ages 25-50, with a secondary audience of male teens. Our target audience are mid to high income, professionals that live in more urban areas, but enjoy being active outdoors after work and on the weekends. Our target audience are hard workers, humble and want to enjoy all that life has to offer – whether that’s on top of a mountain or an ocean wave. They hike, bike, skateboard, surf or any other sport that gets them outside. They are husbands, brothers and fathers – there for their family and friends.

Our brand is sophisticated, adventurous and has a sense of humor. Many of our competitors either focus on the rugged outdoors or are more pretentious. We are in-between. We are free spirited and love the fresh air. Our products are trustworthy with no toxic chemicals or harsh ingredients. We are all-natural and provide high-quality, premium products that our audience expects and deserves.

Target Market(s)

Men, ages 25-54 who are high-earning professionals, yet enjoy getting outdoors and being active on the weekends - hiking, biking, surfing, skateboarding and more.

Industry/Entity Type

Men's skincare

Font styles to use
Sans Serif

Requirements
Must have
• See attachments
Nice to have
• We would prefer to a have a premium, slightly more modern looking design that will appeal to our target audience and slightly higher price point.
Should not have
• Please do not include an icon for the fragrance, i.e. cinnamon sticks. However, we do need some differentiation for the fragrance, i.e. color, etc. as it will be on the shelf with other fragrances.

```html
<!DOCTYPE html>
<html lang="en">
<head>
<meta charset="utf-8">
<title>Trail Hale — Citrus and Cedar Soap Box</title>
<link href="https://fonts.googleapis.com/css2?family=Alfa+Slab+One&family=Fira+Sans+Condensed:ital,wght@0,400;1,400;1,500&family=Jost:wght@400;500&display=swap" rel="stylesheet">
<style>
  :root {
    --navy: #0e2a47;
    --navy-deep: #0b2139;
    --green: #157a16;
    --green-deep: #0f6512;
    --kraft: #c9a777;
    --ink: #2e2b26;
    --white: #ffffff;
    --accent: #e0443c;
    --backdrop: #9a9a9a;
  }
  * { box-sizing: border-box; margin: 0; padding: 0; }
  html, body { width: 1200px; height: 864px; overflow: hidden; }
  body {
    background: radial-gradient(ellipse at 50% 40%, #b3b3b3 0%, var(--backdrop) 70%, #858585 100%);
    position: relative;
    font-family: "Fira Sans Condensed", sans-serif;
  }
  .carton { position: absolute; top: 222px; width: 560px; }
  .carton--front { left: 28px; }
  .carton--back { left: 612px; }

  .flap, .panel { position: relative; width: 560px; overflow: hidden; }
  .flap { height: 64px; }
  .panel { height: 330px; }
  .shape { position: absolute; inset: 0; width: 100%; height: 100%; }

  /* front flap */
  .claims {
    position: absolute; left: 18px; top: 10px; width: 280px;
    color: var(--white); font-style: italic; font-size: 14px; line-height: 1.35;
    display: flex; flex-wrap: wrap; column-gap: 16px;
  }
  .claims li { list-style: none; }
  .claims li::before { content: "\2713\00a0"; font-style: normal; }
  .site-callout { position: absolute; right: 22px; top: 10px; text-align: right; color: var(--white); }
  .site-callout__lead { font-style: italic; font-size: 14px; }
  .site-callout__url { font-family: "Alfa Slab One", serif; font-size: 17px; letter-spacing: 1px; }

  /* brand name */
  .brand {
    position: absolute; left: 28px; top: 150px;
    display: flex; align-items: center; gap: 10px;
  }
  .brand__mark { width: 20px; height: 20px; background: var(--accent); }
  .brand__name {
    font-family: "Fira Sans Condensed", sans-serif; font-weight: 400;
    font-size: 26px; color: var(--white);
  }

  /* front kraft copy */
  .title { font-family: "Alfa Slab One", serif; color: var(--green); text-transform: uppercase; line-height: 0.92; }
  .front-title { position: absolute; left: 252px; top: 34px; font-size: 58px; }
  .scent { position: absolute; left: 240px; top: 222px; color: var(--ink); font-family: "Jost", sans-serif; }
  .scent__note { font-size: 21px; letter-spacing: 1.5px; font-weight: 500; }
  .scent__type { font-size: 14px; margin-top: 2px; }
  .net-weight { position: absolute; left: 212px; bottom: 18px; font-family: "Jost", sans-serif; font-size: 13px; color: var(--ink); }
  .grit-stamp {
    position: absolute; right: 28px; bottom: 26px; width: 92px; height: 92px; border-radius: 50%;
    border: 2px dashed var(--ink); display: flex; align-items: center; justify-content: center;
  }
  .grit-stamp span {
    font-size: 12px; color: var(--green); white-space: nowrap;
    padding: 1px 3px; border: 1.5px solid var(--green); border-radius: 3px;
  }

  /* back flap */
  .distributor { position: absolute; left: 22px; top: 12px; color: var(--white); font-style: italic; font-size: 13px; line-height: 1.35; }

  /* back navy column */
  .back-info { position: absolute; left: 18px; top: 20px; width: 205px; color: var(--white); }
  .back-title { color: var(--white); font-size: 24px; margin-bottom: 12px; }
  .back-heading { font-family: "Alfa Slab One", serif; font-size: 13px; letter-spacing: 1px; text-transform: uppercase; margin-top: 6px; }
  .back-copy { font-size: 13px; line-height: 1.25; font-style: italic; }

  /* back kraft copy */
  .pitch { position: absolute; left: 268px; top: 28px; width: 272px; color: var(--navy); }
  .pitch__heading { font-family: "Alfa Slab One", serif; font-size: 21px; line-height: 1.1; text-transform: uppercase; letter-spacing: 1px; }
  .pitch__body { font-style: italic; font-size: 14.5px; line-height: 1.3; margin-top: 10px; }
  .back-brand { position: absolute; left: 268px; bottom: 26px; display: flex; align-items: center; gap: 8px; }
  .back-brand__mark { width: 14px; height: 14px; background: var(--accent); }
  .back-brand__name { font-family: "Fira Sans Condensed", sans-serif; font-weight: 400; font-size: 17px; color: var(--navy); }
  .origin-badge { position: absolute; right: 26px; bottom: 20px; width: 48px; height: 48px; background: var(--white); }
</style>
</head>
<body>

<section class="carton carton--front" aria-label="Front of box">
  <div class="flap">
    <svg class="shape" viewBox="0 0 560 64" preserveAspectRatio="none" aria-hidden="true">
      <rect width="560" height="64" fill="var(--navy-deep)"/>
      <polygon points="318,0 560,0 560,64 296,64" fill="var(--green-deep)"/>
    </svg>
    <ul class="claims">
      <li>Handcrafted</li>
      <li>No harsh chemicals</li>
      <li>Sustainably sourced</li>
    </ul>
    <div class="site-callout">
      <p class="site-callout__lead">Check out all our products at</p>
      <p class="site-callout__url">TRAILHALE.COM</p>
    </div>
  </div>
  <div class="panel">
    <svg class="shape" viewBox="0 0 560 330" preserveAspectRatio="none" aria-hidden="true">
      <rect width="560" height="330" fill="var(--kraft)"/>
      <polygon points="0,0 232,0 194,330 0,330" fill="var(--navy)"/>
      <polygon points="232,0 241,0 203,330 194,330" fill="var(--green)"/>
    </svg>
    <div class="brand">
      <span class="brand__mark" aria-hidden="true"></span>
      <p class="brand__name">Trail Hale</p>
    </div>
    <h1 class="title front-title">Citrus<br>and<br>Cedar</h1>
    <div class="scent">
      <p class="scent__note">SWEET &amp; SPICY</p>
      <p class="scent__type">Men’s Natural Soap</p>
    </div>
    <p class="net-weight">5 Oz. Bar</p>
    <div class="grit-stamp"><span>MEDIUM GRIT</span></div>
  </div>
</section>

<section class="carton carton--back" aria-label="Back of box">
  <div class="flap">
    <svg class="shape" viewBox="0 0 560 64" preserveAspectRatio="none" aria-hidden="true">
      <rect width="560" height="64" fill="var(--green-deep)"/>
    </svg>
    <p class="distributor">Distributed by:<br>K&amp;M Goods Duluth, MN 55802</p>
  </div>
  <div class="panel">
    <svg class="shape" viewBox="0 0 560 330" preserveAspectRatio="none" aria-hidden="true">
      <rect width="560" height="330" fill="var(--kraft)"/>
      <polygon points="0,0 222,0 246,330 0,330" fill="var(--navy)"/>
      <polygon points="222,0 231,0 255,330 246,330" fill="var(--green)"/>
    </svg>
    <div class="back-info">
      <h2 class="title back-title">Citrus<br>and<br>Cedar</h2>
      <p class="back-heading">Ingredients:</p>
      <p class="back-copy">Vegetable Oil Blend (Olive Oil, Organic Sustainable Palm Oil, Coconut Oil, Shea Butter, Sunflower Oil), Water, Sodium Hydroxide, Beeswax, Cinnamon Essential Oil, Honey, Ground Cinnamon.</p>
      <p class="back-heading">Directions:</p>
      <p class="back-copy">Lather, rinse and repeat.</p>
    </div>
    <div class="pitch">
      <h3 class="pitch__heading">Real ingredients<br>for real guys.</h3>
      <p class="pitch__body">Bring the outdoors in using real, natural ingredients on your skin. Traditional bar soap contains harsh chemical ingredients that can be harmful to you and the environment. Lather up with Trail Hale’s handcrafted, all-natural soap and feel the difference.</p>
    </div>
    <div class="back-brand">
      <span class="back-brand__mark" aria-hidden="true"></span>
      <span class="back-brand__name">Trail Hale</span>
    </div>
    <div class="origin-badge" aria-hidden="true"></div>
  </div>
</section>

</body>
</html>
```